Business card for Luxury Portable Restroom Trailer company

We are a Luxury Portable Restroom Trailer Company Called FALCRIDGE HIRES. Based in Orange County California. We provide portable restroom trailers for events, such as, Weddings, Concerts, Charity events, Sporting events, Tournaments, Corporate events, ect. We rent and Sell the Luxury restrooms. Our colors are white, grey, and Orange. As you will see in the logo we uploaded.
There are 2 people in the company so the names and titles will change for the 3 people but card will remain the same. Here is the information for each Person: Dwight Penner CFO 555 318-0476
next Person: Leon Marchetti VP 555 318-0476
Next Person: Owen Marchetti CEO 555 318-0476
Information to include on the card: Luxury Restroom Trailers Rental and Sales. Weddings, Concerts, Charity, Sporting and Corp. Events.

```html
<!DOCTYPE html>
<html lang="en">
<head>
<meta charset="utf-8">
<title>FALCRIDGE HIRES — Business Card</title>
<link rel="stylesheet" href="https://fonts.googleapis.com/css2?family=Montserrat:wght@400;500;700;800&display=swap">
<style>
  :root {
    --orange: #f26a21;
    --grey: #4b4b4d;
    --grey-light: #6a6a6c;
    --white: #ffffff;
    --charcoal: #262626;
    --charcoal-deep: #1c1c1c;
    --page: #e9e9ea;
  }
  * { box-sizing: border-box; margin: 0; padding: 0; }
  html, body {
    width: 1200px; height: 900px; overflow: hidden;
    background: var(--page);
    font-family: "Montserrat", sans-serif;
  }
  .sheet {
    width: 1200px; height: 900px;
    display: flex; flex-direction: column; align-items: center; justify-content: center;
    gap: 40px;
  }
  .card {
    width: 630px; height: 360px;
    border-radius: 22px;
    position: relative;
    overflow: hidden;
    box-shadow: 0 6px 18px rgba(0,0,0,0.12);
  }

  /* Front */
  .card-front { background: var(--white); }
  .brand {
    position: absolute; top: 58px; right: 48px;
    font-weight: 800; font-size: 34px; letter-spacing: 1px;
    color: var(--orange);
  }
  .person {
    position: absolute; top: 166px; left: 48px; width: 258px;
    text-align: right;
  }
  .person-name {
    font-weight: 700; font-size: 24px; letter-spacing: 1px;
    color: var(--orange); text-transform: uppercase; white-space: nowrap;
  }
  .person-title {
    font-weight: 400; font-size: 17px; color: var(--grey); margin-top: 2px;
  }
  .divider {
    position: absolute; top: 160px; left: 322px;
    width: 1.5px; height: 78px; background: var(--orange);
  }
  .contact {
    position: absolute; top: 158px; left: 340px;
    list-style: none;
  }
  .contact li {
    display: flex; align-items: center; gap: 8px;
    font-size: 15px; color: var(--grey); line-height: 27px;
  }
  .contact svg { width: 13px; height: 13px; flex: none; fill: var(--orange); }
  .tagline {
    position: absolute; left: 48px; right: 40px; top: 268px;
    font-weight: 700; font-size: 16px; color: var(--orange);
  }
  .events {
    position: absolute; left: 48px; right: 40px; top: 298px;
    font-weight: 400; font-size: 15.5px; color: var(--grey);
  }

  /* Back */
  .card-back { background: var(--charcoal); }
  .back-pattern {
    position: absolute; inset: 0;
    background: radial-gradient(circle at 70% 30%, #303030 0%, var(--charcoal) 55%, var(--charcoal-deep) 100%);
  }
  .back-mark {
    position: absolute; left: 70px; bottom: 62px;
    display: flex; align-items: center; gap: 14px;
  }
  .back-mark-ring {
    width: 56px; height: 56px; border-radius: 50%;
    border: 4px solid var(--orange);
  }
  .back-mark-name {
    font-weight: 800; font-size: 20px; letter-spacing: 1px; color: var(--orange);
  }
</style>
</head>
<body>
<main class="sheet">
  <section class="card card-front" aria-label="Card front">
    <div class="brand">FALCRIDGE HIRES</div>

    <div class="person">
      <div class="person-name">Owen Marchetti</div>
      <div class="person-title">CEO</div>
    </div>

    <div class="divider"></div>

    <ul class="contact">
      <li>
        <svg viewBox="0 0 16 16" aria-hidden="true"><path d="M3.6 1.2l2.3 2.6-1.3 1.8c.9 2 2.4 3.5 4.5 4.6l1.8-1.3 2.6 2.3-1.3 2.7C6.9 13.7 2.3 9.1 1 3.8z"/></svg>
        555 318-0476
      </li>
      <li>
        <svg viewBox="0 0 16 16" aria-hidden="true"><path d="M1 3h14v10H1zM2.5 4.5L8 9l5.5-4.5z" fill-rule="evenodd"/></svg>
        owen@falcridgehires.com
      </li>
      <li>
        <svg viewBox="0 0 16 16" aria-hidden="true"><path d="M8 1a7 7 0 100 14A7 7 0 008 1zm0 1.6c.9 1 1.5 2.6 1.6 4.4H6.4C6.5 5.2 7.1 3.6 8 2.6zM6.4 9h3.2c-.1 1.8-.7 3.4-1.6 4.4-.9-1-1.5-2.6-1.6-4.4z"/></svg>
        www.falcridgehires.com
      </li>
    </ul>

    <p class="tagline">Luxury Restroom Trailers Rental and Sales</p>
    <p class="events">Weddings / Concerts / Charity / Sporting / Corp</p>
  </section>

  <section class="card card-back" aria-label="Card back">
    <div class="back-pattern" role="img" aria-label="Tonal repeating brand pattern on charcoal"></div>
    <div class="back-mark">
      <div class="back-mark-ring"></div>
      <div class="back-mark-name">FALCRIDGE HIRES</div>
    </div>
  </section>
</main>
</body>
</html>
```